Medical Practice and Business Coaching Website Design

I need a professional website designed for a medical business, TQP Medical.
The website will be hosted on Vorluna (similar design functionality as ZEPT).

About the website:
Pages for the website:
- Home page (a brief overview of the company with a section for "Ultrasound Clinics" and "Coaching and Courses" that link to these pages with all the info and packages for these sections)
- About Us (section for company info and info about Delphine Ashcombe, founder and business coach)
- Ultrasound Clinics (all the info about ultrasound, our packages, links to book, gallery of 3D/4D images, FAQs, social media links)
- Coaching and Courses (All of our coaching package info, course info with a waiting list sign up, section for free business download resources, social media links, blog posts)
- Contact Us (info for our harrowgate ultrasound location and bookings with a map, contact form, email and phone details)

Pages that are also needed but not visible in the top menu:
- Blog Page
- Waiting List Page x2 (Dubbo pop-up 3D clinic, Online Course)
- Thanks for subscribing page

We have a company logo and a logo for both the ultrasound clinics and the Coaching sides of the business. They are attached as well as the HEX codes for the branding colours. Ideally the company areas of the site will be in the blue, purple and teal colours. The ultrasound clinics page will be mostly in the purple with the "clinics" logo featuring on the page.
The courses and coaching page will be dominant in the blue branding colours with accents of purple and teal. The courses logo will be somewhere on the page too.

About our company:
Our company has 2 separate businesses which will have their own pages on the website.
We have a medical imaging business which specialises in ultrasound. We have 3 locations/services:
- Harrowgate Ultrasound: open Fridays and the occasional saturday. Our main focus and where the focus on the clinical page needs to be.
- East Corrimbal Ultrasound: Currently closed, no re-opening date and unlikely to reopen.
- Pop-up clinics: most commonly occur in Dubbo. occasionally in Parkes. Dates for next pop-up will be announced in the future.

Our Harrowgate practice offers both diagnostic ultrasound (referral from doctor) for all areas of the body and 3d/4d pregnancy ultrasounds for entertainment purposes.
The content for the ultrasound clinics part of the website can be found on the current harrowgate ultrasound website: harrowgateultrasound.com.au
This website will be replaced by the new company site. All of the info on this site will end up on the clinics page of the new company website.

The second part of the company is a coaching and courses service for medical professionals who want to start or grow their business.
We currently have coaching packages for 1-on-1 online advice and guidance.

Coaching: all take place on Meetly and can be recorded for them to watch again after. Notes, documents and links that are discussed are provided after session

- FREE 15 minute session: discuss current business or business idea, if and how I can help and potential things they can do. One per client

- Single Coaching Session - 1hr with Delphine

- Silver coaching package: 1 x 1hr Coaching Call with Delphine
Unlimited Email with Delphine for 1 month
Access to our Private Circlet Group to network with other medical professionals and business owners

- Silver Coaching Package With Social Media Management:
As above with 1 month Social Media Management (15 posts, Circlet and Instagram)

- Gold coaching package: 2 x 1hr Coaching Calls with Delphine
Access to our Private Circlet

- Gold Coaching Package With Social Media Management:

- Business Sidekick Package: Unlimited Coaching Calls
Unlimited SMS
Unlimited Emails
Social Media Management (Circlet and Instagram, 1 post per day) Valued at over $700
Business Masterclass (something different each month...social media, medicare, website, branding, live events, etc)

Enrollment for our first course opens in May and clients can join the waitlist in the meantime.
Course is aimed at medical professionals who want to grow their patient numbers and create an online presence for their business.
Ideal for: small practices where the owner does everything, not necessarily familiar with marketing/social media/websites, goes to the very basics and steps through everything in getting a logo, branding, website, building social media pages, creating content.

Course name to come but it will be something like "helpful marketing in healthcare" or "the business of healthcare"

We will also have a blog on the website and a podcast (in the future).

I would like a testimonial on at least the clinics page and the coaching page. Here is one for each but I have more if need be:
Coaching: "I knew I wanted to start my own business but I had no idea where to begin. It would have been easy to abort my dreams of starting my own business had it not been for the direction and unwavering support of Delphine from TQP medical. Delphine dissected the process into manageable bit sized pieces for me and worked tirelessly behind the scenes ensuring everything was on track. Her friendly, warm and approachable manner
equated to more than her just being my business coach, she has now become a friend.
Thank you!!"

Ultrasound testimonial: "Amazing service! Best ultrasound experience I’ve had. Super friendly and informative staff. Great technology. If I didn’t live so far away I’d go to Harrowgate for all my ultrasounds!"

I would also like a section for a welcome video (yet to be recorded) on the home page, ultrasound clinics page and coaching/courses page.

I've attached the company logo and the sub-logos in different formats. There is also a head shot of Delphine for the about us page, an image of Delphine with a coaching client for the coaching page and multiple 3D ultrasound images for the gallery on the clinics page.

Target Market(s)

Mostly targeted at medical professionals. Pregnant women and anyone needing an ultrasound are the targets for the clinics page

Industry/Entity Type

Healthcare

Number of Pages Required

5+ page

Colors
0054AA
0677BA
7BADD7
CADEEF
E8F1F8
0094D4
00A9DD
6FCCEA
C7EBF8
E9F6FB
00AB8E
00BBA5
67D7C9
C6EFE9
E9F9F6
A7469A
B969AE
D3A5CF
EDDBEB
F8F0F9
6B429C
8869AF
B7A5CE
E3DAEB
F3F0F8

```html
<!DOCTYPE html>
<html lang="en">
<head>
<meta charset="utf-8">
<title>TQP Medical</title>
<link href="https://fonts.googleapis.com/css2?family=Playfair+Display:wght@400;700;900&family=Lora:wght@400;500&family=Open+Sans:wght@400&display=swap" rel="stylesheet">
<style>
:root{
  --purple:#5b3592;
  --purple-ink:#3b2f6b;
  --lavender:#e4e3f2;
  --lavender-card:#ebe7f5;
  --teal:#1f97a4;
  --slate:#555868;
  --ink:#2b2b33;
  --text:#3d3d45;
  --white:#ffffff;
  --footer:#252427;
  --quote:#b9b7c2;
}
*{box-sizing:border-box;margin:0;padding:0}
html,body{width:1200px;height:3841px;overflow:hidden}
body{position:relative;font-family:"Lora",Georgia,serif;color:var(--text);background:var(--white)}
.abs{position:absolute}
.heading{font-family:"Playfair Display",Georgia,serif}
.btn{position:absolute;display:flex;align-items:center;justify-content:center;gap:10px;background:var(--teal);color:var(--white);font-family:"Playfair Display",Georgia,serif;font-size:13px;letter-spacing:1.5px;text-transform:uppercase;text-decoration:none}

/* hero */
.hero{left:0;top:0;width:1200px;height:686px;background:linear-gradient(100deg,#6f5f58 0%,#9a8e89 30%,#c9c4c2 55%,#bdb9b9 75%,#8f8d90 100%)}
.brand{left:115px;top:15px;width:80px;display:flex;flex-direction:column;align-items:center;gap:4px}
.brand-mark{width:70px;height:70px;border-radius:50%;background:var(--purple)}
.brand-name{font-family:"Lora",Georgia,serif;font-size:14px;color:var(--purple);letter-spacing:1px;text-align:center;line-height:1.1}
.nav{left:212px;top:46px;font-family:"Playfair Display",Georgia,serif;font-size:13px;color:var(--ink);text-transform:uppercase}
.nav span{position:absolute;white-space:nowrap;top:0}
.btn-book{left:832px;top:36px;width:124px;height:40px}
.btn-contact{left:963px;top:36px;width:125px;height:40px;background:transparent;border:2px solid var(--teal);color:var(--teal)}
.hero-title{left:112px;top:268px;font-size:64px;font-weight:900;color:var(--white);letter-spacing:1px;font-family:"Playfair Display",Georgia,serif}
.btn-hero{left:112px;top:368px;width:168px;height:46px}
.play{left:802px;top:327px;display:flex;align-items:center;gap:10px;color:var(--white);font-family:"Playfair Display",Georgia,serif;font-size:14px;text-decoration:underline}

/* purple band */
.band{left:0;top:686px;width:1200px;height:414px;background:var(--purple)}
.about-card{left:149px;top:468px;width:373px;height:549px;background:var(--white);padding:12px}
.about-inner{width:100%;height:100%;background:var(--lavender-card);position:relative;text-align:center}
.about-photo{position:absolute;left:13px;top:18px;width:323px;height:233px;background:linear-gradient(160deg,#9c9c9c,#4a4a4a)}
.about-title{position:absolute;left:0;right:0;top:270px;font-size:25px;letter-spacing:1.5px;color:var(--ink);font-weight:400}
.about-text{position:absolute;left:14px;right:14px;top:313px;font-size:16px;line-height:25px;color:var(--text)}
.btn-about{left:89px;top:459px;width:170px;height:47px}
.loc-card{left:563px;top:704px;width:525px;height:313px;background:var(--white);padding:22px 18px}
.loc-title{font-size:25px;letter-spacing:1px;color:var(--ink);font-weight:400;margin-bottom:14px}
.loc-name{font-family:"Playfair Display",Georgia,serif;font-size:13px;letter-spacing:1px;color:var(--ink);margin-bottom:6px}
.loc-text{font-size:16px;line-height:27px;color:var(--text);margin-bottom:30px}

/* coaching */
.coaching{left:0;top:1100px;width:1200px;height:761px;background:var(--lavender)}
.sec-title{position:absolute;left:0;width:1200px;text-align:center;font-family:"Playfair Display",Georgia,serif;font-size:25px;letter-spacing:2px;color:var(--ink)}
.rule{left:112px;top:1223px;width:976px;height:2px;background:var(--purple-ink)}
.sub{left:200px;top:1240px;width:800px;text-align:center;font-size:16px;line-height:25px}
.course{top:1299px;width:308px;height:475px;background:var(--slate);color:var(--white);text-align:center;padding:11px 9px}
.course-img{width:290px;height:193px;margin:0 auto}
.course h3{font-family:"Playfair Display",Georgia,serif;font-weight:700;font-size:21px;line-height:28px;letter-spacing:.5px;margin-top:18px;text-transform:uppercase}
.course p{font-size:15.5px;line-height:27.5px;margin-top:22px;padding:0 18px}
.course p.tight{padding:0}

/* testimonial */
.quote-mark{left:157px;top:2030px}
.avatar{left:533px;top:2010px;width:134px;height:134px;border-radius:50%;background:linear-gradient(180deg,#c9c9d4,#6d7796)}
.t-label{left:0;top:2160px;width:1200px;text-align:center;font-family:"Playfair Display",Georgia,serif;font-size:20px;color:#5d5d6a;letter-spacing:.5px}
.t-text{left:165px;top:2192px;width:870px;text-align:center;font-size:14.5px;line-height:25px;color:#4a4a52}

/* blog */
.blog{left:0;top:2396px;width:1200px;height:1200px;background:var(--lavender)}
.post{left:112px;width:976px;height:289px;background:var(--white)}
.post-img{position:absolute;left:24px;top:20px;width:316px;height:248px}
.post h3{position:absolute;left:365px;top:32px;font-family:"Playfair Display",Georgia,serif;font-weight:700;font-size:20px;color:var(--ink);letter-spacing:.3px}
.post p{position:absolute;left:365px;width:500px;font-size:16px;line-height:27.5px}
.post .p1{top:67px}.post .p2{top:132px}
.post .btn{left:365px;top:204px;width:170px;height:47px}

/* footer */
.footer{left:0;top:3596px;width:1200px;height:245px;background:var(--footer);color:var(--white)}
.socials{left:516px;top:58px;display:flex;gap:44px}
.socials span{width:24px;height:24px;border-radius:50%;background:var(--white);display:block}
.f-links{left:0;width:1200px;top:124px;display:flex;justify-content:center;gap:38px;font-family:"Playfair Display",Georgia,serif;font-size:13px;letter-spacing:1px}
.copy{left:0;width:1200px;top:180px;text-align:center;font-family:"Open Sans",Arial,sans-serif;font-size:13px}
</style>
</head>
<body>

<section class="abs hero" role="img" aria-label="Photo of two smiling clinicians seated beside an ultrasound machine in a clinic room"></section>

<div class="abs brand">
  <span class="brand-mark"></span>
  <span class="brand-name">TQP<br>MEDICAL</span>
</div>

<nav class="abs nav">
  <span style="left:0">Home</span>
  <span style="left:80px">About Us</span>
  <span style="left:183px">Ultrasound Clinics</span>
  <span style="left:366px">Coaching and Courses</span>
  <span style="left:569px">FAQs</span>
</nav>
<a class="btn btn-book">Book Now</a>
<a class="btn btn-contact">Contact Us</a>

<h1 class="abs hero-title">TQP MEDICAL</h1>
<a class="btn btn-hero">Learn More</a>
<div class="abs play">
  <svg width="44" height="44" viewBox="0 0 44 44"><circle cx="22" cy="22" r="22" fill="#fff"/><path d="M17 13 L31 22 L17 31 Z" fill="#1f97a4"/></svg>
  <span>PLAY VIDEO</span>
</div>

<section class="abs band"></section>

<article class="abs about-card">
  <div class="about-inner">
    <div class="about-photo" role="img" aria-label="Black and white portrait photo of the company founder"></div>
    <h2 class="heading about-title">ABOUT OUR COMPANY:</h2>
    <p class="about-text">Perspiciatis unde omnis iste natus error sit voluptatem accusantium doloremque laudantium, totam rem aperiam, eaque ipsa quae ab illo inventore veritatis et quasi architecto beatae</p>
    <a class="btn btn-about">Learn More</a>
  </div>
</article>

<article class="abs loc-card">
  <h2 class="heading loc-title">LOCATIONS/SERVICES:</h2>
  <div class="loc-name">HARROWGATE ULTRASOUND:</div>
  <p class="loc-text">open Fridays and the occasional saturday. Our main focus and where the focus on the clinical page needs to be.</p>
  <div class="loc-name">EAST CORRIMBAL ULTRASOUND:</div>
  <p class="loc-text">Currently closed, no re-opening date and unlikely to reopen.</p>
</article>

<section class="abs coaching"></section>
<h2 class="sec-title" style="top:1180px">COACHING AND COURSES</h2>
<div class="abs rule"></div>
<p class="abs sub">all take place on Meetly and can be recorded for them to watch again after. Notes, documents and links that are discussed are provided after session</p>

<article class="abs course" style="left:112px">
  <div class="course-img" role="img" aria-label="Photo of an ultrasound probe on a pregnant belly" style="background:linear-gradient(135deg,#7fb2d6,#e8eef4)"></div>
  <h3>Free 15 Minute<br>Session:</h3>
  <p>open Fridays and the occasional saturday. Our main focus and where the focus on the clinical page needs to be.</p>
</article>
<article class="abs course" style="left:446px">
  <div class="course-img" role="img" aria-label="Photo of a doctor performing an ultrasound scan" style="background:linear-gradient(135deg,#c9d3dc,#eef1f3)"></div>
  <h3>Silver Coaching<br>Package:</h3>
  <p class="tight">1 x 1hr Coaching Call with Delphine<br>Unlimited Email with Delphine for 1 month</p>
  <p class="tight" style="margin-top:12px">Access to our Private Circlet Group to network with other medical professionals and business owners</p>
</article>
<article class="abs course" style="left:781px">
  <div class="course-img" role="img" aria-label="Photo of a sonographer scanning a patient" style="background:linear-gradient(135deg,#e6e8ea,#9c8f88)"></div>
  <h3>Silver Coaching Package with Social Media Management:</h3>
  <p style="margin-top:12px">open Fridays and the occasional saturday. Our main focus and where the focus on the clinical page needs to be.</p>
</article>

<h2 class="sec-title" style="top:1940px">TESTIMONIAL</h2>
<svg class="abs quote-mark" width="124" height="92" viewBox="0 0 124 92" aria-hidden="true">
  <path d="M30 92 C10 92 0 78 0 60 C0 30 20 8 52 0 L55 8 C38 14 28 26 27 40 C45 40 58 50 58 66 C58 82 46 92 30 92 Z" fill="#b9b7c2"/>
  <path d="M96 92 C76 92 66 78 66 60 C66 30 86 8 118 0 L121 8 C104 14 94 26 93 40 C111 40 124 50 124 66 C124 82 112 92 96 92 Z" fill="#b9b7c2"/>
</svg>
<div class="abs avatar" role="img" aria-label="Round portrait photo of a coaching client"></div>
<div class="abs t-label">COACHING:</div>
<p class="abs t-text">"I knew I wanted to start my own business but I had no idea where to begin. It would have been easy to abort my dreams of starting my own business had it not been for the direction and unwavering support of Delphine from TQP medical. Delphine dissected the process into manageable bit sized pieces for me and worked tirelessly behind the scenes ensuring everything was on track. Her friendly, warm and approachable manner equated to more than her just being my business coach, she has now become a friend. Thank you!!"</p>

<section class="abs blog"></section>
<h2 class="sec-title" style="top:2474px">BLOG</h2>

<article class="abs post" style="top:2555px">
  <div class="post-img" role="img" aria-label="Photo of hands holding ultrasound probes by a machine" style="background:linear-gradient(135deg,#9fb0c2,#e9edf2)"></div>
  <h3>DOLOR SIT AMET CONSECTETUR ADIPISCING</h3>
  <p class="p1">Lorem ipsum dolor sit amet,consectetur adipiscing elit.Lorem ipsum dolor sit amet,consectetur adipiscing elit.</p>
  <p class="p2">Orsit amet,consectetur adipiscing elit.Lorem ipsum dolor sit amet,consectetur adipiscing elit.</p>
  <a class="btn">Learn More <svg width="8" height="12" viewBox="0 0 8 12"><path d="M1 1 L6 6 L1 11" stroke="#fff" stroke-width="2" fill="none"/></svg></a>
</article>
<article class="abs post" style="top:2888px">
  <div class="post-img" role="img" aria-label="Photo of a pregnancy ultrasound scan in progress" style="background:linear-gradient(135deg,#d8c6d6,#8e5a6e)"></div>
  <h3>DOLOR SIT AMET CONSECTETUR ADIPISCING</h3>
  <p class="p1">Lorem ipsum dolor sit amet,consectetur adipiscing elit.Lorem ipsum dolor sit amet,consectetur adipiscing elit.</p>
  <p class="p2">Orsit amet,consectetur adipiscing elit.Lorem ipsum dolor sit amet,consectetur adipiscing elit.</p>
  <a class="btn">Learn More <svg width="8" height="12" viewBox="0 0 8 12"><path d="M1 1 L6 6 L1 11" stroke="#fff" stroke-width="2" fill="none"/></svg></a>
</article>
<article class="abs post" style="top:3222px">
  <div class="post-img" role="img" aria-label="Photo of a patient lying down during an ultrasound examination" style="background:linear-gradient(135deg,#e2c99a,#2c3a6a)"></div>
  <h3>DOLOR SIT AMET CONSECTETUR ADIPISCING</h3>
  <p class="p1">Lorem ipsum dolor sit amet,consectetur adipiscing elit.Lorem ipsum dolor sit amet,consectetur adipiscing elit.</p>
  <p class="p2">Orsit amet,consectetur adipiscing elit.Lorem ipsum dolor sit amet,consectetur adipiscing elit.</p>
  <a class="btn">Learn More <svg width="8" height="12" viewBox="0 0 8 12"><path d="M1 1 L6 6 L1 11" stroke="#fff" stroke-width="2" fill="none"/></svg></a>
</article>

<footer class="abs footer">
  <div class="abs socials" aria-label="Social links"><span></span><span></span><span></span></div>
  <div class="abs f-links"><span>TERMS</span><span>PRIVACY</span><span>COOKIES POLICY</span></div>
  <div class="abs copy">Copyright © 2022 | All Rights Reserved</div>
</footer>

</body>
</html>
```